Bramble Hounds Dog Behaviour, Training and Natural Healthcare Website

Hey there,
I need a webpage designed for my new business. It needs to be something authentic, new, fresh and representative of my business ethos. I operate out of Newcastle, NSW. I believe my job is to keep dogs alive and in their home by promoting communication and connection between dogs and their owners. This can't be achieved through training and behaviour alone. Nutritional guidance and environmental adaptation are often needed to complete the package and increase the success rate for these programs. I provide practical services such as walking coaching, nutrition profiling, behavioural modification, puppy minding, board and train programs for puppies and young dogs, training, basic and complex skills training, physical therapies and natural healthcare options. In effect taking care of the whole dog.
My motto is = Happy dogs, happy owners.
My catch cry is = promoting communication and connection between dogs and their owners.

I have in mind pages that can also link to other pages when an icon is clicked. I need a homepage, sections to explain what each of my services do (4 - which could be independent pages so I can attach photos) and a gallery. I want to have multi page function, an online capability for future retail, ability to amend and update content myself, an online booking and payment facility. My interests lie in I have seen many successes via and environmental modifications.
I've attached the logo which features prominently on my business card and Facebook page. The corporate colours are Blue with a splash of red and white. The dog being held in the healing hands must feature.

Thanks!

Target Market(s)

Australian Pet Dog Owners

Industry/Entity Type

Communication

Coding

Colors
0355a3
ec1f27
ffffff

Requirements
Must have
• The business colours (blue with a splash of red and white), the dog in the healing hands
Should not have
• Pawprints or cartoon animals

```html
<!DOCTYPE html>
<html lang="en">
<head>
<meta charset="utf-8">
<title>Bramble Hounds Dog Behaviour, Training and Natural Healthcare</title>
<link href="https://fonts.googleapis.com/css2?family=Roboto:wght@400;500;700&display=swap" rel="stylesheet">
<style>
:root{
  --blue:#0355a3;
  --blue-dark:#0a4fa6;
  --red:#ec1f27;
  --white:#ffffff;
  --grey-bg:#f1f1f1;
  --text:#333;
  --muted:#666;
  --footer-dark:#1b1b1b;
}
*{box-sizing:border-box;margin:0;padding:0}
html,body{width:705px;height:1200px;overflow:hidden;background:var(--white)}
body{font-family:'Roboto',sans-serif;color:var(--text);position:relative}

.site-header{height:91px;background:linear-gradient(#1591dc,#0a5cb8);position:relative}
.brand{position:absolute;left:48px;top:13px;width:94px;text-align:center;color:var(--white)}
.brand-mark{width:42px;height:42px;border-radius:50%;background:var(--white);border:3px solid #c3343b;margin:0 auto 4px}
.brand-name{font-size:11px;font-weight:700;letter-spacing:.3px;white-space:nowrap}
.brand-tag{font-size:5px;letter-spacing:.2px;margin-top:1px;white-space:nowrap}
.main-nav{position:absolute;left:238px;top:45px;display:flex;gap:22px}
.main-nav a{color:var(--white);font-size:8.5px;text-decoration:none}
.login{position:absolute;left:591px;top:38px;width:62px;height:22px;background:var(--white);color:var(--blue);font-size:10px;font-weight:500;display:flex;align-items:center;justify-content:center;letter-spacing:.5px}

.hero{height:326px;position:relative;background:
  linear-gradient(180deg,rgba(0,0,0,0) 55%,rgba(196,92,24,.55) 85%,rgba(170,70,20,.7) 100%),
  radial-gradient(ellipse 140px 180px at 29% 62%,rgba(238,236,228,.85),rgba(238,236,228,0) 70%),
  radial-gradient(ellipse 120px 220px at 66% 45%,rgba(40,70,120,.75),rgba(40,70,120,0) 75%),
  linear-gradient(100deg,#6f8a2e 0%,#c9a23a 30%,#8c9a3c 55%,#b9822c 80%,#7d8f34 100%)}
.hero-title{position:absolute;left:373px;top:108px;width:279px;height:95px;background:rgba(0,0,0,.55);color:var(--white);padding:15px 24px}
.hero-title h1{font-size:29px;font-weight:500;line-height:1}
.hero-title p{font-size:22px;font-weight:500;margin-top:9px}
.hero-arrow{position:absolute;top:147px;width:21px;height:21px;border-radius:50%;background:rgba(255,255,255,.75);display:flex;align-items:center;justify-content:center}

.welcome{height:157px;text-align:center;padding:25px 53px 0;border-bottom:1px solid #ddd}
.section-title{color:var(--red);font-weight:400;font-size:16px}
.welcome p{font-size:8.8px;line-height:16px;color:#444;margin-top:9px}
.btn{display:inline-block;background:linear-gradient(#1f79cf,var(--blue-dark));color:var(--white);border-radius:3px;text-decoration:none}
.btn-lg{font-size:9.5px;padding:7px 10px;margin-top:11px}
.btn-sm{font-size:6.5px;padding:6px 6px;font-weight:500}

.services{height:238px;background:var(--grey-bg);position:relative;padding:21px 52px 0;border-bottom:1px solid #ddd}
.services .section-title{font-size:14px}
.carousel-nav{position:absolute;right:52px;top:18px;display:flex;gap:4px}
.service-grid{display:flex;gap:22px;margin-top:12px}
.service{width:134px}
.service-photo{height:88px;border:3px solid var(--white);box-shadow:0 0 2px #999}
.service h3{color:var(--red);font-size:7.3px;font-weight:500;margin-top:13px}
.service p{font-size:6.8px;line-height:10px;color:var(--muted);margin:6px 0 8px;text-align:justify}

.therapies{height:194px;padding:37px 52px 0;display:flex;gap:20px}
.therapies-photo{width:179px;height:127px;border:3px solid var(--white);box-shadow:0 0 2px #999;flex:none;background:
  radial-gradient(ellipse 50px 35px at 55% 70%,rgba(240,236,226,.9),rgba(240,236,226,0) 75%),
  linear-gradient(135deg,#4f7f34 0%,#8fb257 45%,#c9d39a 75%,#a7b47a 100%)}
.therapies h2{font-size:12.5px;color:var(--red);font-weight:400;margin-top:4px}
.therapies p{font-size:7.3px;line-height:15px;margin:6px 0 10px;text-align:justify;color:#222}

.site-footer{height:127px;background:var(--blue);color:var(--white);display:flex;padding:27px 0 0 53px;position:relative}
.foot-col h4{font-size:8px;font-weight:500;margin-bottom:12px}
.foot-col li{list-style:none;font-size:6.2px;margin-bottom:6px}
.testimonial{font-size:5.4px;font-style:italic;line-height:9.7px;color:#dbe6f4;width:124px;padding-left:2px}
.client{font-size:6.2px;margin-top:6px;color:#dbe6f4}
.newsletter p{font-size:6px;line-height:9px;color:#cdd9ea;width:120px}
.email{width:122px;height:16px;background:#eee;color:#555;font-size:5.5px;padding:5px 6px;margin-top:7px}
.subscribe{display:inline-block;background:#333;font-size:5.5px;font-weight:700;padding:4px 8px;margin-top:8px;border-radius:2px}
.social li{display:flex;align-items:center;gap:7px;margin-bottom:9px;font-size:6.4px;list-style:none}
.social i{width:16px;height:16px;border-radius:50%;background:var(--white);display:block}
.social i.red{background:#e0443c}

.bottom-bar{height:67px;background:var(--footer-dark);color:var(--white);text-align:center;font-size:6.8px;padding-top:24px;position:relative}
.bottom-bar .links{word-spacing:1px}
.bottom-bar .copy{margin-top:10px}
</style>
</head>
<body>

<header class="site-header">
  <div class="brand">
    <div class="brand-mark"></div>
    <div class="brand-name">BRAMBLE HOUNDS</div>
    <div class="brand-tag">HAPPY DOGS, HAPPY OWNERS</div>
  </div>
  <nav class="main-nav">
    <a href="#">HOME</a><a href="#">ABOUT US</a><a href="#">SERVICES</a><a href="#">NEWS</a><a href="#">HEALTHCARE</a><a href="#">CONTACTS</a>
  </nav>
  <a class="login">LOGIN</a>
</header>

<section class="hero" role="img" aria-label="Two small dogs sitting on autumn leaves looking up at their owner in jeans">
  <div class="hero-arrow" style="left:15px"><svg width="8" height="10" viewBox="0 0 8 10"><path d="M6 1L2 5l4 4" stroke="#333" stroke-width="1.5" fill="none"/></svg></div>
  <div class="hero-arrow" style="left:667px"><svg width="8" height="10" viewBox="0 0 8 10"><path d="M2 1l4 4-4 4" stroke="#333" stroke-width="1.5" fill="none"/></svg></div>
  <div class="hero-title"><h1>DOG BEHAVIOUR</h1><p>STUDY AND TRAINING</p></div>
</section>

<section class="welcome">
  <h2 class="section-title">WELCOME TO BRAMBLE HOUNDS</h2>
  <p>Lorem Ipsum has been the industry's standard dummy text ever since the 1500s, when an unknown printer took a galley of type and scrambled it to make a type specimen book. It has survived not only five centuries, but also the leap into electronic typesetting, remaining essentially unchanged. It was popularised in the 1960s with the release</p>
  <a class="btn btn-lg" href="#">Read More</a>
</section>

<section class="services">
  <h2 class="section-title">SERVICE</h2>
  <div class="carousel-nav">
    <svg width="17" height="17" viewBox="0 0 17 17"><circle cx="8.5" cy="8.5" r="7.5" fill="none" stroke="#111" stroke-width="1.3"/><path d="M10 5L6.5 8.5 10 12" stroke="#111" stroke-width="1.5" fill="none"/></svg>
    <svg width="17" height="17" viewBox="0 0 17 17"><circle cx="8.5" cy="8.5" r="7.5" fill="none" stroke="#111" stroke-width="1.3"/><path d="M7 5l3.5 3.5L7 12" stroke="#111" stroke-width="1.5" fill="none"/></svg>
  </div>
  <div class="service-grid">
    <article class="service">
      <div class="service-photo" role="img" aria-label="Owner walking two dogs on a leash along a park path" style="background:linear-gradient(180deg,#4e7d2f 0%,#86a955 45%,#b9b7a4 70%,#9e9b8c 100%)"></div>
      <h3>WALKING COACHING</h3>
      <p>Lorem Ipsum has been the industry's standard dummy text ever since the 1500s, when an unknown printer</p>
      <a class="btn btn-sm" href="#">READ MORE</a>
    </article>
    <article class="service">
      <div class="service-photo" role="img" aria-label="Golden retriever lying beside a yellow food bowl" style="background:radial-gradient(ellipse 35px 20px at 50% 78%,#f2c21c,rgba(242,194,28,0) 80%),linear-gradient(135deg,#fbf8f1 0%,#ecdcb5 50%,#d7b77a 100%)"></div>
      <h3>NUTRITION PROFILING</h3>
      <p>Lorem Ipsum has been the industry's standard dummy text ever since the 1500s, when an unknown printer</p>
      <a class="btn btn-sm" href="#">READ MORE</a>
    </article>
    <article class="service">
      <div class="service-photo" role="img" aria-label="Woman crouching to train a white dog outdoors" style="background:linear-gradient(180deg,#e3b640 0%,#8fae4c 40%,#5f8a3a 65%,#3c5f86 100%)"></div>
      <h3>BEHAVIOURAL MODIFICATION</h3>
      <p>Lorem Ipsum has been the industry's standard dummy text ever since the 1500s, when an unknown printer</p>
      <a class="btn btn-sm" href="#">READ MORE</a>
    </article>
    <article class="service">
      <div class="service-photo" role="img" aria-label="Woman on a sofa holding a small white puppy" style="background:linear-gradient(120deg,#d9b79a 0%,#e7d3c2 40%,#6d7a55 70%,#f4f2ee 100%)"></div>
      <h3>PUPPY MINDING</h3>
      <p>Lorem Ipsum has been the industry's standard dummy text ever since the 1500s, when an unknown printer</p>
      <a class="btn btn-sm" href="#">READ MORE</a>
    </article>
  </div>
</section>

<section class="therapies">
  <div class="therapies-photo" role="img" aria-label="Dog leaping for a frisbee held by its owner in a park"></div>
  <div>
    <h2>PHYSICAL THERAPIES AND NATURAL HEALTHCARE</h2>
    <p>Lorem Ipsum has been the industry's standard dummy text ever since the 1500s, when an unknown printer took a galley of type and scrambled it to make a type specimen book. It has survived not only five centuries, but also the leap into electronic typesetting, remaining essentially unchanged. It was popularised in the 1960s with the release of Typeleaf sheets containing Lorem Ipsum passages, and more recently with desktop publishing software like Quillset Layout including versions of Lorem Ipsum</p>
    <a class="btn btn-sm" href="#">READ MORE</a>
  </div>
</section>

<footer class="site-footer">
  <div class="foot-col" style="width:102px">
    <h4>Quick Links</h4>
    <ul><li>Home</li><li>About Us</li><li>What We Do</li><li>Resources</li><li>Contribute</li></ul>
  </div>
  <div class="foot-col" style="width:108px">
    <h4>Support Links</h4>
    <ul><li>Partners</li><li>Gallery</li><li>Contact Us</li><li>Privacy Policy</li><li>Term of Use</li></ul>
  </div>
  <div class="foot-col" style="width:172px">
    <h4>Client's Testimonials</h4>
    <p class="testimonial">“ Lorem Ipsum has been the industry's standard dummy text ever since the 1500s, when an unknown printer took a galley of type and scrambled it to make a type specimen book. It has survived not only five centuries. ”</p>
    <p class="client">Client name, City</p>
  </div>
  <div class="foot-col newsletter" style="width:164px">
    <h4>Newsletters Sign Up</h4>
    <p>Sign up for our daily email by entering your information below</p>
    <div class="email">Email address</div>
    <span class="subscribe">SUBSCRIBE</span>
  </div>
  <div class="foot-col">
    <h4>Follow us</h4>
    <ul class="social"><li><i></i>Pawbook</li><li><i></i>Chirper</li><li><i class="red"></i>Circles+</li></ul>
  </div>
</footer>

<div class="bottom-bar">
  <div class="links">Privacy Policy &nbsp;| &nbsp;Terms Conditions &nbsp;| &nbsp;Sitemap &nbsp;| &nbsp;Contact Us</div>
  <div class="copy">Copyright © 2014 &nbsp;All Rights Reserved</div>
</div>

</body>
</html>
```